BOLD & MINIMALIST DESIGN NEEDED

We want a very bold but minimalistic business card design that is impactful and utilizes both sides of the business card. Our current logo is included for your use.

We want bold fonts and good use of negative space. We don't want the logo to overpower the design.

Target Market(s)

Professionals who are building new commercial buildings.

Industry/Entity Type

Construction

Contact Information for Business Card

Name, Title, email, office phone, cell phone, website

Font styles to use
Serif
Sans Serif

Requirements
Must have
• Bold design!

```html
<!DOCTYPE html>
<html lang="en">
<head>
<meta charset="utf-8">
<title>Ridgecrest Design + Build — Business Card</title>
<link href="https://fonts.googleapis.com/css2?family=Archivo:wght@400;800&display=swap" rel="stylesheet">
<style>
  :root {
    --page-bg: #d2d2d2;
    --card-green: #4a7a1c;
    --card-green-deep: #2c4a0c;
    --accent-lime: #8cd43a;
    --text-white: #ffffff;
    --text-soft: #eef5e4;
  }
  * { box-sizing: border-box; margin: 0; padding: 0; }
  html, body {
    width: 1200px; height: 802px; overflow: hidden;
    background: var(--page-bg);
    font-family: "Archivo", Arial, sans-serif;
  }
  .stage {
    position: relative; width: 1200px; height: 802px;
    display: flex; align-items: center; justify-content: center; gap: 50px;
  }
  .card {
    position: relative; width: 540px; height: 309px;
    border-radius: 16px; overflow: hidden;
    background: radial-gradient(ellipse at 55% 40%, var(--card-green) 0%, var(--card-green-deep) 100%);
    box-shadow: 0 14px 30px rgba(0,0,0,0.28);
    color: var(--text-white);
  }
  .card-front::after {
    content: ""; position: absolute; right: 0; top: 0; bottom: 0; width: 6px;
    background: var(--accent-lime);
  }
  .company-name {
    display: flex; align-items: center; gap: 8px;
    font-weight: 800; color: var(--text-white); line-height: 1; white-space: nowrap;
  }
  .company-square { width: 12px; height: 12px; background: var(--accent-lime); flex: none; }
  .card-front .company-name { position: absolute; top: 36px; right: 36px; font-size: 18px; }
  .card-back .company-name {
    position: absolute; inset: 0; justify-content: center; font-size: 30px; gap: 12px;
  }
  .card-back .company-square { width: 18px; height: 18px; }
  .identity { position: absolute; left: 0; top: 112px; padding-left: 30px; }
  .identity::before {
    content: ""; position: absolute; left: 0; top: 4px; width: 10px; height: 44px;
    background: var(--accent-lime);
  }
  .person-name { font-size: 26px; font-weight: 800; color: var(--accent-lime); text-transform: uppercase; letter-spacing: 0.3px; }
  .person-title { font-size: 15px; font-weight: 400; margin-top: 4px; }
  .contact-list { position: absolute; left: 30px; bottom: 26px; list-style: none; }
  .contact-list li { display: flex; align-items: center; gap: 10px; font-size: 14px; line-height: 22px; color: var(--text-soft); }
  .contact-list svg { width: 14px; height: 14px; fill: var(--accent-lime); flex: none; }
  .address { position: absolute; right: 36px; bottom: 92px; text-align: right; font-size: 14px; line-height: 20px; }
</style>
</head>
<body>
<main class="stage">
  <section class="card card-front" aria-label="Card front">
    <p class="company-name"><span class="company-square"></span>Ridgecrest Design + Build</p>
    <div class="identity">
      <h1 class="person-name">Marcus Hale</h1>
      <p class="person-title">Founder &amp; CEO</p>
    </div>
    <ul class="contact-list">
      <li><svg viewBox="0 0 24 24"><path d="M6.6 10.8a15 15 0 006.6 6.6l2.2-2.2c.3-.3.7-.4 1-.2 1.1.4 2.3.6 3.6.6.6 0 1 .4 1 1V20c0 .6-.4 1-1 1A17 17 0 013 4c0-.6.4-1 1-1h3.5c.6 0 1 .4 1 1 0 1.3.2 2.5.6 3.6.1.3 0 .7-.2 1z"/></svg>012-555-610-204</li>
      <li><svg viewBox="0 0 24 24"><path d="M7 2h10a2 2 0 012 2v16a2 2 0 01-2 2H7a2 2 0 01-2-2V4a2 2 0 012-2zm0 3v13h10V5z"/></svg>044-555-318-762</li>
      <li><svg viewBox="0 0 24 24"><path d="M2 21l21-9L2 3v7l15 2-15 2z"/></svg>info@ridgecrest.com</li>
      <li><svg viewBox="0 0 24 24"><path d="M12 2a10 10 0 100 20 10 10 0 000-20zm0 2a8 8 0 110 16 8 8 0 010-16zM4 11h16v2H4zm7-7h2v16h-2z"/></svg>www.ridgecrest.com</li>
    </ul>
    <p class="address">4410 Harbor Point Blvd<br>210-B, FL 32541</p>
  </section>
  <section class="card card-back" aria-label="Card back">
    <p class="company-name"><span class="company-square"></span>Ridgecrest Design + Build</p>
  </section>
</main>
</body>
</html>
```